"Fight Back" banner ad design

We have sketched the design and have images to consider including. We are looking for something striking, FIGHT BACK! with a clenched fist image, then a fading images of variance.png and hi-bill.png in the background. Tag line "Fight your water bill with your own data" optionally include "Tally Mode" rivo3196 logo, KPMT Design, LLC based in San Diego CA. Pre-order now, visit https://www.fundbeacon.com/rivometer @rivo3196, info@rivo3196.com

"Fight your water bill with your own data"

```html
<!DOCTYPE html>
<html lang="en">
<head>
<meta charset="utf-8">
<title>Fight Back – rivo3196</title>
<link rel="stylesheet" href="https://fonts.googleapis.com/css2?family=Lexend:wght@400;500;600;700&family=Montserrat:wght@800&family=Arimo:wght@400;700&display=swap">
<style>
  :root {
    --teal: #3a7886;
    --teal-dark: #1f5864;
    --teal-light: #8ccbdc;
    --navy: #0e3559;
    --ink: #111111;
    --paper: #ffffff;
    --btn-top: #6aa7ea;
    --btn-bottom: #2d6bc2;
    --skin-light: #ecc6a8;
    --skin-mid: #d79f7c;
  }
  * { margin: 0; padding: 0; box-sizing: border-box; }
  html, body { width: 1200px; height: 663px; overflow: hidden; background: var(--paper); }
  .banner { position: relative; width: 1200px; height: 663px; overflow: hidden; background: var(--paper); font-family: "Lexend", sans-serif; }

  .bill-backdrop {
    position: absolute; left: 268px; top: 0; width: 456px; height: 663px;
    background: linear-gradient(180deg, rgba(222,229,233,.5), rgba(240,243,245,.3) 60%, rgba(214,225,230,.45));
  }

  .fist-photo {
    position: absolute; left: 0; top: 0; width: 720px; height: 470px;
    background: radial-gradient(ellipse 250px 235px at 340px 250px, var(--skin-mid) 0%, var(--skin-light) 45%, rgba(236,198,168,.35) 75%, rgba(255,255,255,0) 100%);
  }

  .headline { position: absolute; left: 490px; top: 22px; width: 696px; height: 94px; }
  .headline text { font-family: "Montserrat", sans-serif; font-weight: 800; font-size: 112px; }

  .tagline {
    position: absolute; left: 730px; top: 134px;
    font-weight: 600; font-size: 43px; line-height: 56px; color: var(--navy); letter-spacing: -0.3px;
  }

  .usage-chart { position: absolute; left: 558px; top: 264px; width: 634px; height: 380px; }
  .usage-chart .title { font-family: "Arimo", sans-serif; font-weight: 700; font-size: 21px; fill: var(--paper); }
  .usage-chart .legend { font-family: "Arimo", sans-serif; font-size: 15px; fill: var(--ink); letter-spacing: .6px; }
  .usage-chart .tick { font-family: "Arimo", sans-serif; font-size: 14px; fill: var(--ink); }

  .preorder-btn {
    position: absolute; left: 14px; top: 462px; width: 344px; height: 44px;
    border-radius: 3px; box-shadow: 0 0 0 4px #e6eef8;
    background: linear-gradient(180deg, var(--btn-top), var(--btn-bottom));
    color: var(--paper); font-family: "Lexend", sans-serif; font-weight: 600; font-size: 31px;
    display: flex; align-items: center; justify-content: center; gap: 34px; text-decoration: none;
  }
  .preorder-btn svg { width: 14px; height: 16px; }

  .contact-lines {
    position: absolute; left: 9px; top: 517px;
    font-weight: 400; font-size: 24px; line-height: 33.5px; color: var(--ink); letter-spacing: -0.2px;
  }
  .brand-mark { position: absolute; left: 440px; top: 598px; display: flex; align-items: center; gap: 6px;
    font-weight: 500; font-size: 19px; color: var(--teal); letter-spacing: .5px; }
  .brand-mark .dot { width: 10px; height: 10px; border-radius: 50%; background: var(--teal); }

  .studio-name { position: absolute; left: 992px; top: 636px; font-family: "Lexend", sans-serif; font-weight: 600; font-size: 25px; color: var(--navy); line-height: 30px; }
</style>
</head>
<body>
<main class="banner">
  <div class="bill-backdrop" role="img" aria-label="Faded water bill statements with rate charges in the background"></div>

  <div class="fist-photo" role="img" aria-label="Photo of a clenched fist crumpling a printed water bill showing fees and charges"></div>

  <svg class="headline" viewBox="0 0 696 94" aria-label="FIGHT BACK!">
    <text x="2" y="88" textLength="690" lengthAdjust="spacingAndGlyphs" fill="none" stroke="var(--paper)" stroke-width="10" stroke-linejoin="round">FIGHT BACK!</text>
    <text x="2" y="88" textLength="690" lengthAdjust="spacingAndGlyphs" fill="var(--teal)">FIGHT BACK!</text>
  </svg>

  <p class="tagline">Fight your water bill<br>with your own data.</p>

  <svg class="usage-chart" viewBox="0 0 634 380" aria-label="Water use in hundred cubic feet, previous year versus current year">
    <rect x="0" y="0" width="634" height="380" fill="var(--paper)" stroke="var(--ink)" stroke-width="1.5"/>
    <rect x="0" y="0" width="634" height="28" fill="var(--teal-dark)"/>
    <text class="title" x="317" y="21" text-anchor="middle">WATER USE IN HCF (Hundred Cubic Feet)</text>

    <rect x="164" y="34" width="17" height="17" fill="var(--teal-light)" stroke="#556" stroke-width=".8"/>
    <text class="legend" x="198" y="48">Previous Year</text>
    <rect x="330" y="34" width="17" height="17" fill="var(--teal-dark)"/>
    <text class="legend" x="362" y="48">Current Year</text>

    <g stroke="var(--ink)" stroke-width="1.2">
      <line x1="34" y1="60" x2="624" y2="60"/><line x1="34" y1="79.75" x2="624" y2="79.75"/>
      <line x1="34" y1="99.5" x2="624" y2="99.5"/><line x1="34" y1="119.25" x2="624" y2="119.25"/>
      <line x1="34" y1="139" x2="624" y2="139"/><line x1="34" y1="158.75" x2="624" y2="158.75"/>
      <line x1="34" y1="178.5" x2="624" y2="178.5"/><line x1="34" y1="198.25" x2="624" y2="198.25"/>
      <line x1="34" y1="218" x2="624" y2="218"/><line x1="34" y1="237.75" x2="624" y2="237.75"/>
      <line x1="34" y1="257.5" x2="624" y2="257.5"/><line x1="34" y1="277.25" x2="624" y2="277.25"/>
      <line x1="34" y1="297" x2="624" y2="297"/><line x1="34" y1="316.75" x2="624" y2="316.75"/>
      <line x1="34" y1="336.5" x2="624" y2="336.5"/><line x1="34" y1="356.25" x2="624" y2="356.25"/>
      <line x1="34" y1="376" x2="624" y2="376"/>
    </g>
    <g class="tick" text-anchor="end">
      <text x="30" y="65">80</text><text x="30" y="84.75">75</text><text x="30" y="104.5">70</text>
      <text x="30" y="124.25">65</text><text x="30" y="144">60</text><text x="30" y="163.75">55</text>
      <text x="30" y="183.5">50</text><text x="30" y="203.25">45</text><text x="30" y="223">40</text>
      <text x="30" y="242.75">35</text><text x="30" y="262.5">30</text><text x="30" y="282.25">25</text>
      <text x="30" y="302">20</text><text x="30" y="321.75">15</text><text x="30" y="341.5">10</text>
      <text x="30" y="361.25">5</text><text x="30" y="381">0</text>
    </g>
    <g stroke="#333" stroke-width=".8">
      <rect x="84" y="269.35" width="20" height="106.65" fill="var(--teal-light)"/>
      <rect x="110" y="285.15" width="20" height="90.85" fill="var(--teal-dark)"/>
      <rect x="183" y="241.7" width="20" height="134.3" fill="var(--teal-light)"/>
      <rect x="209" y="297" width="20" height="79" fill="var(--teal-dark)"/>
      <rect x="282" y="300.95" width="20" height="75.05" fill="var(--teal-light)"/>
      <rect x="308" y="297" width="20" height="79" fill="var(--teal-dark)"/>
      <rect x="381" y="257.5" width="20" height="118.5" fill="var(--teal-light)"/>
      <rect x="407" y="63.95" width="20" height="312.05" fill="var(--teal-dark)"/>
      <rect x="480" y="277.25" width="20" height="98.75" fill="var(--teal-light)"/>
      <rect x="506" y="107.4" width="20" height="268.6" fill="var(--teal-dark)"/>
      <rect x="579" y="277.25" width="20" height="98.75" fill="var(--teal-light)"/>
      <rect x="605" y="87.65" width="20" height="288.35" fill="var(--teal-dark)"/>
    </g>
  </svg>

  <a class="preorder-btn" href="#">Pre-order now
    <svg viewBox="0 0 14 16" aria-hidden="true"><path d="M3 2 L10 8 L3 14" fill="none" stroke="currentColor" stroke-width="3"/></svg>
  </a>

  <p class="contact-lines">
    Change "LLC based in San Diego CA<br>
    to a San Diego startup<br>
    Visit https://www.fundbeacon.com<br>
    rivometer@rivo3196, info@rivo3196.com
  </p>

  <div class="brand-mark"><span class="dot"></span>rivo3196</div>

  <div class="studio-name">KPMT Design</div>
</main>
</body>
</html>
```